I need a business card design for a new business based in South West Australia.
I specialize in residential window cleaning & general handyman maintenance.

Dale Marsh - 412 SILVER HAWK DETAILING
- Window Cleaning
- House Maintenance

```html
<!DOCTYPE html>
<html lang="en">
<head>
<meta charset="utf-8">
<title>412 Silver Hawk Detailing – Business Card</title>
<link rel="stylesheet" href="https://fonts.googleapis.com/css2?family=Oswald:wght@600&family=Open+Sans:wght@400;600;700&display=swap">
<style>
  :root {
    --backdrop: #9a9a98;
    --card-black: #000000;
    --brand-blue: #0d55a0;
    --swoosh-grey: #d6d6d6;
    --ink-white: #ffffff;
  }
  * { box-sizing: border-box; margin: 0; padding: 0; }
  html, body { width: 1200px; height: 900px; overflow: hidden; }
  body {
    background: var(--backdrop);
    position: relative;
    font-family: "Open Sans", Arial, sans-serif;
  }
  .card {
    position: absolute;
    width: 560px;
    height: 320px;
    overflow: hidden;
    box-shadow: 0 6px 18px rgba(0,0,0,0.25);
  }
  .card-front {
    left: 560px; top: 90px;
    background: var(--card-black);
    display: flex; flex-direction: column;
    align-items: center; justify-content: center;
    color: var(--ink-white);
    text-align: center;
  }
  .front-name {
    font-family: "Oswald", Arial, sans-serif;
    font-weight: 600;
    font-size: 38px;
    letter-spacing: 0.5px;
    line-height: 1;
  }
  .front-tagline {
    font-weight: 700;
    font-size: 13.5px;
    letter-spacing: 1.2px;
    margin-top: 8px;
  }
  .card-back { left: 80px; top: 470px; background: var(--card-black); }
  .card-back > .back-swoosh { position: absolute; inset: 0; }
  .back-brand {
    position: absolute; left: 26px; top: 145px; width: 240px;
    display: flex; align-items: center; gap: 8px;
  }
  .brand-dot {
    width: 14px; height: 14px; border-radius: 50%;
    background: var(--brand-blue); flex: none;
  }
  .back-name {
    font-weight: 700;
    font-size: 15px;
    letter-spacing: 0.4px;
    color: var(--ink-white);
    white-space: nowrap;
  }
  .contact {
    position: absolute; right: 30px; top: 0; bottom: 0;
    display: flex; flex-direction: column; justify-content: center;
    align-items: flex-end; text-align: right;
    color: var(--ink-white);
  }
  .person-name { font-weight: 700; font-size: 17px; }
  .person-role { font-size: 14px; margin-bottom: 22px; }
  .contact-line {
    display: flex; align-items: center; gap: 8px;
    font-size: 14px; line-height: 1.35;
  }
  .contact-icon { width: 12px; height: 12px; fill: var(--ink-white); flex: none; }
  .contact-gap { height: 18px; }
  .address { text-align: right; }
</style>
</head>
<body>
  <section class="card card-front" aria-label="Card front">
    <h1 class="front-name">412 SILVER HAWK DETAILING</h1>
    <p class="front-tagline">WINDOW CLEANING &amp; HOUSE MAINTENANCE</p>
  </section>

  <section class="card card-back" aria-label="Card back">
    <svg class="back-swoosh" viewBox="0 0 560 320" width="560" height="320" aria-hidden="true">
      <path d="M245,0 C350,80 330,240 140,320 L560,320 L560,0 Z" fill="var(--swoosh-grey)"/>
      <path d="M268,0 C375,85 355,245 175,320 L560,320 L560,0 Z" fill="var(--brand-blue)"/>
    </svg>

    <div class="back-brand">
      <span class="brand-dot"></span>
      <p class="back-name">412 SILVER HAWK DETAILING</p>
    </div>

    <div class="contact">
      <p class="person-name">Dale Marsh</p>
      <p class="person-role">Managing Director</p>
      <p class="contact-line">08 9555 0142
        <svg class="contact-icon" viewBox="0 0 24 24" aria-hidden="true"><path d="M6.6 10.8a15 15 0 0 0 6.6 6.6l2.2-2.2c.3-.3.7-.4 1-.2 1.1.4 2.3.6 3.6.6.6 0 1 .4 1 1V20c0 .6-.4 1-1 1A17 17 0 0 1 3 4c0-.6.4-1 1-1h3.5c.6 0 1 .4 1 1 0 1.3.2 2.5.6 3.6.1.3 0 .7-.2 1z"/></svg>
      </p>
      <p class="contact-line">hello@silverhawkwa.au
        <svg class="contact-icon" viewBox="0 0 24 24" aria-hidden="true"><path d="M2 5h20v14H2z M4 7v.5l8 5 8-5V7l-8 5z" fill-rule="evenodd"/></svg>
      </p>
      <div class="contact-gap"></div>
      <div class="contact-line">
        <p class="address">12 Harbour Road, Bunbury<br>Western Australia, 6230</p>
        <svg class="contact-icon" viewBox="0 0 24 24" aria-hidden="true"><path d="M12 2a7 7 0 0 0-7 7c0 5 7 13 7 13s7-8 7-13a7 7 0 0 0-7-7zm0 9.5a2.5 2.5 0 1 1 0-5 2.5 2.5 0 0 1 0 5z"/></svg>
      </div>
    </div>
  </section>
</body>
</html>
```